redesign my website bluekeelvoyages.net and make it user friendly

I already have a website, bluekeelvoyages.net, and want a redesign in WordPress with Elementor Pro, using the same text/content. The goal is to improve:

Design quality (colors, fonts, spacing, visual flow)
User experience (easy navigation, clear offers)
Conversion readiness (calls-to-action, trust signals, booking flow)
Technical side (SEO basics, fast speed, full mobile responsiveness)

The site should look modern, clean, fun, engaging, interactive and optimized for speed and usability.

I would like the 11 page to be consolidate dto 6 as follows: Home (main landing, highlights)

Sailboat Trips (all packages, itineraries, pricing)
Boats (fleet details, features, photos)
How It Works (booking process, FAQs, travel info, what to expect)
Blog
Contact Us (form, WhatsApp, phone, etc.)

Target Market(s)

sailboat trip customers for San Blas Islands in Panama

Industry/Entity Type

Travel, Boat Tour Agency

Coding

Coded - Design and coding required

Number of Pages Required

3 page

Font styles to use
Sans Serif
Other font styles liked:
• Oswalg and sans serif

Colors
0054AA
0677BA
7BADD7
CADEEF
E8F1F8
0094D4
00A9DD
6FCCEA
C7EBF8
E9F6FB
FFC000
F8CF3A
FAE287
FDF2CF
FEFAEE
F0912C
F2A743
F7CA91
FBE8D2
FDF5EE

Requirements
Must have
• Home (main landing, highlights) Sailboat Trips (all packages, itineraries, pricing) Boats (fleet details, features, photos) How It Works (booking process, FAQs, travel info, what to expect) Blog (updates, travel tips, inspiration) Contact Us (form, WhatsApp, phone, etc.)
Nice to have
• I want it to look professionla and be very user friendy to entice people to contact me to book boat trips
Should not have
• a store

```html
<!DOCTYPE html>
<html lang="en">
<head>
<meta charset="utf-8">
<title>Blue Keel Voyages — Sailing San Blas</title>
<link href="https://fonts.googleapis.com/css2?family=Oswald:wght@500;600&family=Lato:wght@400;700&display=swap" rel="stylesheet">
<style>
:root{
  --navy:#0a2a5c;
  --deep:#0054AA;
  --blue:#0677BA;
  --sky:#0094D4;
  --btn:#1a8ad6;
  --pale:#E8F1F8;
  --mist:#CADEEF;
  --gold:#F0912C;
  --ink:#2b2f36;
  --muted:#555c66;
  --footer:#0b1e3b;
  --white:#fff;
}
*{box-sizing:border-box;margin:0;padding:0}
html,body{width:1200px;height:4655px;overflow:hidden}
body{font-family:'Lato',sans-serif;color:var(--ink);background:var(--white);position:relative}
h1,h2,h3,.display{font-family:'Oswald',sans-serif;font-weight:600}
.abs{position:absolute}
.btn{display:inline-flex;align-items:center;justify-content:center;background:var(--btn);color:#fff;border-radius:22px;font-weight:700;font-size:15px;height:42px;padding:0 32px}

.promo{left:0;top:0;width:1200px;height:32px;background:var(--navy);color:#fff;font-size:13px;display:flex;align-items:center;justify-content:center}
.header{left:0;top:32px;width:1200px;height:113px;background:#fff}
.brand{left:104px;top:40px;display:flex;align-items:center;gap:12px}
.brand-dot{width:30px;height:30px;border-radius:50%;background:var(--sky)}
.brand-name{font-family:'Oswald',sans-serif;font-weight:600;font-size:34px;color:var(--navy)}
.nav{left:503px;top:42px;display:flex;gap:14px;align-items:center;font-size:15px;color:var(--ink)}
.nav a{padding:7px 13px;border-radius:18px}
.nav .active{background:var(--btn);color:#fff}
.lang{left:952px;top:36px;width:136px;height:42px;padding:0}

.hero{top:145px;height:556px;width:396px;color:#fff}
.hero .photo{position:absolute;inset:0}
.hero h2{position:absolute;left:48px;top:300px;font-size:36px;font-weight:500}
.hero p{position:absolute;left:48px;top:358px;width:300px;font-size:17px;line-height:25px}
.hero .btn{position:absolute;left:48px;top:458px;height:40px;padding:0 32px}

.who{left:0;top:701px;width:1200px;height:492px;text-align:center}
.who h2{position:absolute;left:0;right:0;top:95px;font-size:44px;color:var(--navy);font-weight:500}
.who p{position:absolute;left:190px;width:820px;top:185px;font-size:20px;line-height:29px;color:var(--ink)}
.who .btn{position:absolute;left:531px;top:339px;width:138px;padding:0}
.deco{position:absolute;top:35px;width:150px;height:200px}

.fleet{left:0;top:1193px;width:1200px;height:768px;background:var(--pale)}
.fleet h2{position:absolute;left:110px;top:62px;font-size:44px;color:var(--navy);font-weight:500}
.fleet .lead{position:absolute;left:112px;top:145px;width:560px;font-size:20px;line-height:28px}
.arrow{position:absolute;top:81px;width:36px;height:36px;border-radius:50%;background:var(--blue)}
.fleet .boat{position:absolute;left:441px;top:231px;width:647px;height:441px;border-radius:16px}
.boat-card{position:absolute;left:112px;top:289px;width:510px;height:325px;background:#fff;border-radius:6px;box-shadow:0 4px 20px rgba(0,40,90,.12);padding:40px 40px}
.boat-card h3{font-size:28px;color:var(--navy);font-weight:500}
.boat-card .tag{font-size:15px;margin-top:10px}
.specs{display:grid;grid-template-columns:150px 130px 130px;row-gap:24px;margin-top:28px;font-size:14px;color:var(--muted)}
.specs span{display:flex;align-items:center;gap:10px}
.boat-card .btn{margin-top:32px;height:42px;padding:0 28px}

.reviews-title{left:0;top:2048px;width:1200px;text-align:center;font-size:44px;color:var(--navy);font-weight:500}
.review{top:2145px;width:316px;height:228px;border:1px solid #dbe3ea;border-radius:8px;padding:26px 22px;font-size:14px;line-height:22px;color:var(--muted)}
.review.hl{background:var(--btn);color:#fff;border-color:var(--btn)}
.stars{color:var(--gold);font-size:17px;letter-spacing:1px;margin-bottom:10px}
.review.hl .stars{color:#fff}

.video{left:112px;top:2463px;width:976px;height:428px;border-radius:12px}
.play{left:562px;top:2638px;width:76px;height:76px;border-radius:50%;background:#fff;display:flex;align-items:center;justify-content:center}

.plans-title{left:0;top:2996px;width:1200px;text-align:center;font-size:44px;color:var(--navy);font-weight:500}
.rule{left:571px;top:3068px;width:58px;height:3px;background:var(--btn)}
.field{height:64px;border:2px solid #d4dbe2;box-shadow:0 2px 6px rgba(0,0,0,.08);background:#fff;font-size:15px;display:flex;align-items:center;padding-left:26px;color:var(--ink)}
.opt{display:flex;align-items:center;gap:12px;font-size:15px;color:var(--ink)}
.opt i{width:20px;height:20px;border-radius:50%;background:#dfe3e7;display:inline-block}
.q{left:112px;top:3330px;font-family:'Oswald',sans-serif;font-weight:500;font-size:19px;color:var(--blue)}
.send{left:531px;top:3627px;width:138px;height:40px;padding:0}
.island{left:0;top:3686px;width:1200px;height:548px}

.footer{left:0;top:4234px;width:1200px;height:421px;background:var(--footer);color:#fff}
.footer h4{font-family:'Lato',sans-serif;font-weight:700;font-size:21px;position:absolute;top:86px}
.footer ul{list-style:none;position:absolute;top:136px;font-size:15px}
.footer li{height:39px}
.footer .about{position:absolute;left:112px;top:134px;width:285px;font-size:14px;line-height:26px}
.social{position:absolute;top:268px;display:flex;gap:18px;left:114px}
.social i{display:block;width:32px;height:32px;border-radius:6px;background:var(--btn)}
.social i+i{background:transparent;border:2px solid #fff;width:24px;height:24px;margin-top:4px}
.contact{position:absolute;left:673px;top:134px;font-size:14px;line-height:24px}
.contact div{display:flex;gap:16px;margin-bottom:22px}
.copy{position:absolute;left:0;right:0;top:4622px;text-align:center;font-size:13px;color:#fff}
</style>
</head>
<body>

<div class="abs promo">August Early Birds - BOOK NOW! $50 Off - Only $545!</div>

<header class="abs header">
  <div class="abs brand"><span class="brand-dot"></span><span class="brand-name">Blue Keel Voyages</span></div>
  <nav class="abs nav">
    <a class="active">Home</a><a>About Us</a><a>Pricing</a><a>Guna Yala</a><a>More ⌄</a>
  </nav>
  <a class="abs btn lang">English ⌄</a>
</header>

<section class="abs hero" style="left:0">
  <div class="photo" role="img" aria-label="Couple on a boat deck at sunset over the sea" style="background:linear-gradient(180deg,#c98a5a 0%,#7a5a4a 35%,#2c3440 70%,#1c2630 100%)"></div>
  <h2>Private Charters</h2>
  <p>All-inclusive catamaran, custom itinerary, flexible options, and crew just for you.</p>
  <a class="btn">Book Now</a>
</section>
<section class="abs hero" style="left:402px">
  <div class="photo" role="img" aria-label="Group snorkelling in clear turquoise water" style="background:linear-gradient(180deg,#5ea7d9 0%,#2f7fb5 40%,#1b5f8a 70%,#0f3f5e 100%)"></div>
  <h2>Shared Charters</h2>
  <p>Affordable group trips—meet new friends, enjoy beaches, clear waters, and great meals.</p>
  <a class="btn">Book Now</a>
</section>
<section class="abs hero" style="left:804px">
  <div class="photo" role="img" aria-label="Cheerful group of travellers on a catamaran deck" style="background:linear-gradient(180deg,#8fb0c6 0%,#6d7f86 40%,#3d4e58 70%,#233541 100%)"></div>
  <h2>Family-Friendly Trips</h2>
  <p>Safe, fun sailing for kids and parents — calm waters, snorkeling, and island hopping.</p>
  <a class="btn">Book Now</a>
</section>

<section class="abs who">
  <div class="deco" role="img" aria-label="Faint sailboat decoration" style="left:50px;background:radial-gradient(ellipse at 50% 60%,#d6ebf8 0%,rgba(214,235,248,0) 70%)"></div>
  <div class="deco" role="img" aria-label="Faint sailboat decoration" style="right:50px;background:radial-gradient(ellipse at 50% 60%,#d6ebf8 0%,rgba(214,235,248,0) 70%)"></div>
  <h2>Who We are</h2>
  <p>We’re sailors and travelers with a love for exploration. When we first arrived in San Blas, its unique beauty and culture left a lasting impression. What began as a stop along our journey soon became something more—we felt a strong connection to this place and a sincere respect for its people, traditions, and way of life.</p>
  <a class="btn">Read More</a>
</section>

<section class="abs fleet">
  <h2>Featured Catamarans</h2>
  <p class="lead">Explore our handpicked fleet—comfort, style, and the perfect way to sail San Blas.</p>
  <span class="arrow" style="left:1004px"><svg width="36" height="36" viewBox="0 0 36 36"><path d="M20 12l-6 6 6 6" stroke="#fff" stroke-width="2.5" fill="none"/></svg></span>
  <span class="arrow" style="left:1053px"><svg width="36" height="36" viewBox="0 0 36 36"><path d="M16 12l6 6-6 6" stroke="#fff" stroke-width="2.5" fill="none"/></svg></span>
  <div class="boat" role="img" aria-label="Aerial view of a white catamaran anchored off a palm island" style="background:linear-gradient(180deg,#5f8a5a 0%,#5fb0b4 25%,#1f6f9a 55%,#0d3f6a 100%)"></div>
  <div class="boat-card">
    <h3>Marea 42</h3>
    <p class="tag">Service that exceeds all expectations!</p>
    <div class="specs">
      <span><svg width="22" height="18"><circle cx="7" cy="6" r="4" stroke="#0677BA" fill="none"/><circle cx="15" cy="6" r="4" stroke="#0677BA" fill="none"/></svg>8 passengers</span>
      <span><svg width="22" height="18"><rect x="2" y="5" width="18" height="10" stroke="#0677BA" fill="none"/></svg>Cabins : 3</span>
      <span><svg width="22" height="18"><rect x="2" y="2" width="18" height="14" stroke="#0677BA" fill="none"/></svg>200 sqft Romm</span>
      <span><svg width="22" height="18"><path d="M2 7a13 13 0 0 1 18 0M5 11a8 8 0 0 1 12 0" stroke="#0677BA" fill="none"/><circle cx="11" cy="15" r="1.5" fill="#0677BA"/></svg>Free Wifi</span>
      <span><svg width="22" height="18"><rect x="3" y="8" width="16" height="8" stroke="#0677BA" fill="none"/><path d="M5 8V3h4" stroke="#0677BA" fill="none"/></svg>Bathrooms : 2</span>
    </div>
    <a class="btn">Info &amp; Price</a>
  </div>
</section>

<h2 class="abs reviews-title">What Our Customers Say</h2>
<div class="abs review" style="left:112px"><div class="stars">★★★★★</div>Everything was absolutely great - from the transfer to the boat crew, the food, and the islands we visited. We really enjoyed the whole experience. The only thing we regret is not having more time to extend the trip in San Blas.</div>
<div class="abs review hl" style="left:441px"><div class="stars">★★★★★</div>My wife and I traveled from the UK to visit the San blas. Our 2 night 3 day trip on a catamaran was a once in a life time experience. It started with a smooth transfer from our hotel in Panama to the boat in the San blas, followed</div>
<div class="abs review" style="left:772px"><div class="stars">★★★★★</div>Absolutely phenomenal experience. We have traveled all around the world and this was one of the best experiences we have ever had. From the beginning of the booking process with Tomas and being matched with a boat and captain, all</div>

<div class="abs video" role="img" aria-label="Video of guests swimming beside a catamaran" style="background:linear-gradient(180deg,#7fb0d6 0%,#c9d6de 30%,#3f7f9a 60%,#1f4f6a 100%)"></div>
<div class="abs play"><svg width="76" height="76" viewBox="0 0 76 76"><circle cx="38" cy="38" r="30" fill="var(--deep)"/><path d="M32 26l16 12-16 12z" fill="#fff"/></svg></div>

<h2 class="abs plans-title">Tell Us Your Travel Plans</h2>
<div class="abs rule"></div>
<div class="abs field" style="left:112px;top:3106px;width:311px">Name</div>
<div class="abs field" style="left:444px;top:3106px;width:311px">Email</div>
<div class="abs field" style="left:776px;top:3106px;width:312px">Whatsapp Number</div>
<div class="abs opt" style="left:112px;top:3194px"><i></i>Private Charter</div>
<div class="abs opt" style="left:268px;top:3196px"><i></i>Shared Charter</div>
<div class="abs field" style="left:112px;top:3238px;width:311px">Number of Passengers</div>
<div class="abs field" style="left:444px;top:3238px;width:311px">Number of Days</div>
<div class="abs field" style="left:776px;top:3238px;width:312px">Date<svg style="position:absolute;right:22px" width="20" height="20"><rect x="1" y="3" width="18" height="16" fill="none" stroke="#1a8ad6" stroke-width="2"/><path d="M1 8h18M6 12h2M10 12h2M14 12h2M6 15h2M10 15h2M14 15h2" stroke="#1a8ad6" stroke-width="2"/></svg></div>
<div class="abs q">What type of experience are you looking for? (Check all that apply)</div>
<div class="abs opt" style="left:112px;top:3387px"><i></i>Relaxing and disconnected</div>
<div class="abs opt" style="left:335px;top:3389px"><i></i>Island-hopping adventure</div>
<div class="abs opt" style="left:552px;top:3389px"><i></i>Snorkeling &amp; marine life</div>
<div class="abs opt" style="left:756px;top:3389px"><i></i>Cultural exchange with the Guna people</div>
<div class="abs opt" style="left:112px;top:3431px"><i></i>Family-friendly</div>
<div class="abs opt" style="left:335px;top:3433px"><i></i>Romantic getaway</div>
<div class="abs opt" style="left:552px;top:3433px"><i></i>Food &amp; drink-focused</div>
<div class="abs opt" style="left:756px;top:3433px"><i></i>Sailing-focused</div>
<div class="abs opt" style="left:112px;top:3474px"><i></i>Budget-friendly</div>
<div class="abs opt" style="left:335px;top:3476px"><i></i>Luxury experience</div>
<div class="abs field" style="left:112px;top:3526px;width:976px">Message</div>
<a class="abs btn send">Send</a>

<div class="abs island" role="img" aria-label="Aerial view of a catamaran moored beside a small palm-covered island" style="background:linear-gradient(180deg,#ffffff 0%,#cfe9ea 18%,#5fb8b0 45%,#2a8fa0 70%,#1a5f7a 100%)"></div>

<footer class="abs footer">
  <h4 style="left:112px">About Us</h4>
  <p class="about">Blue Keel Voyages offers all-inclusive island-hopping, snorkeling, and immersive cultural experiences— rusted by travelers worldwide.</p>
  <div class="social"><i></i><i></i><i></i></div>
  <h4 style="left:485px">Main Links</h4>
  <ul style="left:485px"><li>Home</li><li>Fleet</li><li>About Us</li><li>Contact</li><li>Pricing</li></ul>
  <h4 style="left:673px">Contact Us</h4>
  <div class="contact" style="top:136px">
    <div><svg width="20" height="22"><path d="M10 21s7-7 7-12a7 7 0 0 0-14 0c0 5 7 12 7 12z" stroke="#fff" fill="none" stroke-width="1.5"/><circle cx="10" cy="9" r="2.5" stroke="#fff" fill="none"/></svg><span>isla coral/ reef cays<br>san blas islands, Panama</span></div>
    <div><svg width="20" height="20"><path d="M4 2l4 1 1 4-2 2a11 11 0 0 0 5 5l2-2 4 1 1 4c-8 1-16-7-15-15z" stroke="#fff" fill="none" stroke-width="1.5"/></svg><span>+573005550142</span></div>
    <div><svg width="20" height="20"><rect x="1" y="4" width="18" height="13" stroke="#fff" fill="none" stroke-width="1.5"/><path d="M1 4l9 7 9-7" stroke="#fff" fill="none" stroke-width="1.5"/></svg><span>hello@bluekeelvoyages.net</span></div>
  </div>
  <h4 style="left:979px">Other Links</h4>
  <ul style="left:980px"><li>Guna Yala</li><li>Itineraries</li><li>Activities</li><li>Blog</li><li>Book Now</li></ul>
</footer>
<p class="copy">Copyright © Blue Keel Voyages. All rights reserved. Privacy Policy &nbsp;|&nbsp; Terms &amp; Conditions</p>

</body>
</html>
```